General Surgeon flyer to be distributed to GPs

I am a general surgeon and I would like to have a flyer designed aiming to introduce myself to GPs.

Name: Dr Tobias Lindqvar MD, FSCS
Address: Suite 9A, Brellam private hospital, 418 Corvell Parade, Harlowvale, VIC, 3987
T: (03) 9587 6102
F: (03) 9463 1178
E: referrals@quillfordsurgeons.com.au
Website: www.quillfordsurgeons.com.au

Tobias is a highly trained general surgeon, having completed extensive surgical training at Tarrowby health, Pellington and Corrigan Health networks. He further specialized by completing a fellowship in Oesophagogastric and Bariatric Surgery at St Aldric’s Hospital Melbourne, one of Victoria’s leading Upper GI surgical centres.

With expertise in both advanced laparoscopic and open surgical techniques, he performs a wide range of procedures involving the gastrointestinal system, abdominal wall hernias, as well as other major and minor general surgical operations. In addition to holding appointments at Tarrowby Health, he also operates at Brellam and Fernwick Private Hospitals.

Dr Lindqvar is committed to providing patient-centred care with a focus on surgical precision, safety, and long-term health outcomes.

He is also fluent in Swedish/Norwegian.
Outside of surgery, Tobias enjoys playings jazz guitar and spending time with his 4-year-old Cavoodle on long walks.

Upper GI & Bariatric Surgery:
Hiatus hernia repair, sleeve gastrectomy, gastric bypass
General Surgery conditions:
Gallbladder Surgery: Laparoscopic cholecystectomy
Hernia Repair: Laparoscopic and open surgery (inguinal,
umbilical, incisional)
Anorectal Procedures: Haemorrhoidectomy, haemorrhoid banding
Hand Surgery: Carpal tunnel release, Lymph Node Biopsy
Ingrown Toenail Surgery
Skin & Soft Tissue Surgery: Skin cancer removal, lipoma and
sebaceous cyst excision
Emergency Surgery: Laparotomy, Appendicectomy, bowel resection
Endoscopy: Diagnostic and therapeutic procedures

```html
<!DOCTYPE html>
<html lang="en">
<head>
<meta charset="utf-8">
<title>Dr Tobias Lindqvar – General Surgeon</title>
<link rel="stylesheet" href="https://fonts.googleapis.com/css2?family=Montserrat:wght@400;500;600;700&family=Questrial&display=swap">
<style>
  :root {
    --green: #3fb54a;
    --blue: #1bb3e8;
    --ink: #2a2a2a;
    --body-ink: #333333;
    --white: #ffffff;
    --page: #ecebe8;
  }
  * { box-sizing: border-box; margin: 0; padding: 0; }
  html, body { width: 1200px; height: 1200px; overflow: hidden; background: var(--page); }
  .flyer {
    position: absolute; left: 197px; top: 30px; width: 806px; height: 1140px;
    background: var(--white); overflow: hidden;
    font-family: "Questrial", sans-serif; color: var(--ink);
    box-shadow: 0 2px 10px rgba(0,0,0,.12);
  }
  .hero-visual {
    position: absolute; left: 0; top: 0; width: 806px; height: 200px;
    background:
      radial-gradient(ellipse 170px 120px at 640px 80px, rgba(120,200,245,.95), rgba(120,200,245,0) 70%),
      linear-gradient(90deg, #ffffff 0%, #eef6fa 35%, #d4ebf6 60%, #78c6ec 100%);
  }
  .hero-fade {
    position: absolute; left: 0; top: 120px; width: 470px; height: 90px;
    background: linear-gradient(180deg, rgba(255,255,255,0), #fff);
  }
  .brand { position: absolute; left: 31px; top: 40px; display: flex; align-items: center; gap: 12px; }
  .brand-dot { width: 80px; height: 80px; border-radius: 50%; background: var(--blue); }
  .brand-name { font-family: "Montserrat", sans-serif; font-weight: 700; font-size: 20px; color: var(--green); line-height: 1.1; width: 120px; }

  .doctor-name {
    position: absolute; left: 33px; top: 196px;
    font-family: "Montserrat", sans-serif; font-weight: 700; font-size: 48px; line-height: 48px;
    color: var(--green); letter-spacing: .5px;
  }
  .doctor-post { position: absolute; left: 35px; top: 292px; font-size: 36px; color: var(--ink); }

  .bio {
    position: absolute; left: 36px; top: 356px; width: 404px;
    font-family: "Montserrat", sans-serif; font-weight: 400;
    font-size: 12.4px; line-height: 16.4px; color: var(--body-ink);
  }
  .bio p + p { margin-top: 15px; }

  .portrait {
    position: absolute; left: 22px; top: 742px; width: 446px; height: 334px;
    background:
      radial-gradient(ellipse 210px 170px at 240px 334px, #4f628f 0%, #6c80a8 50%, rgba(150,175,210,0) 100%),
      linear-gradient(180deg, #ffffff 0%, #e5f3fa 45%, #b9e1f3 100%);
  }
  .web-bar {
    position: absolute; left: 24px; top: 1076px; width: 444px; height: 64px;
    background: var(--green); color: var(--white);
    font-family: "Montserrat", sans-serif; font-weight: 600; font-size: 19px; letter-spacing: .6px;
    display: flex; align-items: center; justify-content: center;
  }

  .services-panel {
    position: absolute; left: 465px; top: 183px; width: 341px; height: 957px;
    background: var(--blue); border-top-left-radius: 70px; color: var(--white);
  }
  .service-list {
    list-style: none; position: absolute; left: 30px; top: 48px; width: 300px;
    border-left: 1.5px solid rgba(255,255,255,.8); padding-left: 14px;
  }
  .service { position: relative; margin-bottom: 17px; }
  .service:last-child { margin-bottom: 0; }
  .service-icon { position: absolute; left: -24px; top: 1px; width: 18px; height: 18px; }
  .service-title { font-family: "Montserrat", sans-serif; font-weight: 700; font-size: 14.2px; letter-spacing: .2px; text-transform: uppercase; }
  .service-desc { font-family: "Montserrat", sans-serif; font-weight: 400; font-size: 12.6px; line-height: 16px; margin-top: 2px; }
  .service-desc.large { font-size: 15.5px; }

  .panel-divider { position: absolute; left: 0; top: 630px; width: 341px; border-top: 1.5px solid rgba(255,255,255,.9); }
  .contact { position: absolute; left: 26px; top: 665px; width: 305px; }
  .contact-name { font-family: "Montserrat", sans-serif; font-weight: 700; font-size: 25px; }
  .contact-post { font-size: 26px; margin-top: 4px; }
  .contact-row { display: flex; align-items: flex-start; gap: 6px; font-size: 13px; line-height: 17px; margin-top: 12px; }
  .contact-row svg { flex: none; margin-top: 2px; }
  .contact-row.pair { gap: 14px; }
  .contact-row .item { display: flex; align-items: center; gap: 5px; }
  .email { font-size: 12px; letter-spacing: -.2px; }

  .credentials { position: absolute; left: 30px; top: 890px; display: flex; align-items: center; gap: 14px; width: 290px; }
  .badge-shield { width: 26px; height: 32px; background: var(--white); border-radius: 2px 2px 13px 13px; flex: none; }
  .credentials-text { font-size: 11.5px; line-height: 14px; flex: 1; }
  .badge-round { width: 34px; height: 34px; border: 2px solid var(--white); border-radius: 50%; flex: none; }
</style>
</head>
<body>
  <main class="flyer">
    <div class="hero-visual" role="img" aria-label="Soft blue medical technology banner with a glowing anatomical graphic"></div>
    <div class="hero-fade"></div>

    <div class="brand">
      <span class="brand-dot"></span>
      <span class="brand-name">Quillford Surgeons</span>
    </div>

    <h1 class="doctor-name">DR. TOBIAS<br>LINDQVAR</h1>
    <div class="doctor-post">MD, FSCS</div>

    <div class="bio">
      <p>Tobias is a highly trained general surgeon, having completed extensive surgical training at Tarrowby health, Pellington and Corrigan Health networks. He further specialized by completing a fellowship in Oesophagogastric and Bariatric Surgery at St Aldric’s Hospital Melbourne, one of Victoria’s leading Upper GI surgical centres.</p>
      <p>With expertise in both advanced laparoscopic and open surgical techniques, he performs a wide range of procedures involving the gastrointestinal system, abdominal wall hernias, as well as other major and minor general surgical operations. In addition to holding appointments at Tarrowby Health, he also operates at Brellam and Fernwick Private Hospitals.</p>
      <p>Dr Lindqvar is committed to providing patient-centred care with a focus on surgical precision, safety, and long-term health outcomes.</p>
      <p>He is also fluent in Swedish/Norwegian.<br>Outside of surgery, Tobias enjoys playing jazz guitar and spending time with his 4-year-old Cavoodle on long walks.</p>
    </div>

    <div class="portrait" role="img" aria-label="Portrait photograph of Dr Tobias Lindqvar in a navy suit on a light blue hexagon background"></div>
    <div class="web-bar">www.quillfordsurgeons.com.au</div>

    <section class="services-panel">
      <ul class="service-list">
        <li class="service">
          <svg class="service-icon" viewBox="0 0 18 18"><path d="M4 2 L14 9 L4 16 L7 9 Z" fill="#fff"/></svg>
          <div class="service-title">Upper GI &amp; Bariatric Surgery:</div>
          <div class="service-desc">Hiatus hernia repair, sleeve gastrectomy, gastric bypass</div>
        </li>
        <li class="service">
          <svg class="service-icon" viewBox="0 0 18 18"><path d="M4 2 L14 9 L4 16 L7 9 Z" fill="#fff"/></svg>
          <div class="service-title">General Surgery conditions:</div>
        </li>
        <li class="service">
          <svg class="service-icon" viewBox="0 0 18 18"><path d="M4 2 L14 9 L4 16 L7 9 Z" fill="#fff"/></svg>
          <div class="service-title">Gallbladder Surgery:</div>
          <div class="service-desc large">Laparoscopic cholecystectomy</div>
        </li>
        <li class="service">
          <svg class="service-icon" viewBox="0 0 18 18"><path d="M4 2 L14 9 L4 16 L7 9 Z" fill="#fff"/></svg>
          <div class="service-title">Hernia Repair:</div>
          <div class="service-desc">Laparoscopic and open surgery<br>(inguinal,umbilical, incisional)</div>
        </li>
        <li class="service">
          <svg class="service-icon" viewBox="0 0 18 18"><path d="M4 2 L14 9 L4 16 L7 9 Z" fill="#fff"/></svg>
          <div class="service-title">Anorectal Procedures:</div>
          <div class="service-desc">Haemorrhoidectomy, haemorrhoid<br>banding</div>
        </li>
        <li class="service">
          <svg class="service-icon" viewBox="0 0 18 18"><path d="M4 2 L14 9 L4 16 L7 9 Z" fill="#fff"/></svg>
          <div class="service-title">Hand Surgery:</div>
          <div class="service-desc">Carpal tunnel release, Lymph Node<br>Biopsy Ingrown Toenail Surgery</div>
        </li>
        <li class="service">
          <svg class="service-icon" viewBox="0 0 18 18"><path d="M4 2 L14 9 L4 16 L7 9 Z" fill="#fff"/></svg>
          <div class="service-title">Skin &amp; Soft Tissue Surgery:</div>
          <div class="service-desc">Skin cancer removal, lipoma and<br>sebaceous cyst excision</div>
        </li>
        <li class="service">
          <svg class="service-icon" viewBox="0 0 18 18"><path d="M4 2 L14 9 L4 16 L7 9 Z" fill="#fff"/></svg>
          <div class="service-title">Emergency Surgery:</div>
          <div class="service-desc">Laparotomy, Appendicectomy, bowel<br>resection</div>
        </li>
        <li class="service">
          <svg class="service-icon" viewBox="0 0 18 18"><path d="M4 2 L14 9 L4 16 L7 9 Z" fill="#fff"/></svg>
          <div class="service-title">Endoscopy:</div>
          <div class="service-desc">Diagnostic and therapeutic procedures</div>
        </li>
      </ul>

      <div class="panel-divider"></div>

      <div class="contact">
        <div class="contact-name">Dr Tobias Lindqvar</div>
        <div class="contact-post">MD, FSCS</div>
        <div class="contact-row">
          <svg width="12" height="14" viewBox="0 0 12 14"><path d="M6 1a4.5 4.5 0 0 0-4.5 4.5C1.5 9 6 13 6 13s4.5-4 4.5-7.5A4.5 4.5 0 0 0 6 1z" fill="none" stroke="#fff" stroke-width="1.4"/><circle cx="6" cy="5.5" r="1.6" fill="#fff"/></svg>
          <span>Suite 9A, Brellam private hospital,<br>418 Corvell Parade, Harlowvale,<br>VIC, 3987</span>
        </div>
        <div class="contact-row pair">
          <span class="item"><svg width="14" height="12" viewBox="0 0 14 12"><path d="M1 4c0-2 3-3 6-3s6 1 6 3v1h-3V3.5H4V5H1z M3 6h8l1.5 5h-11z" fill="#fff"/></svg>(03) 9587 6102</span>
          <span class="item"><svg width="14" height="13" viewBox="0 0 14 13"><rect x="3" y="1" width="8" height="4" fill="none" stroke="#fff" stroke-width="1.3"/><rect x="1" y="5" width="12" height="7" fill="#fff"/></svg>(03) 9463 1178</span>
        </div>
        <div class="contact-row">
          <svg width="11" height="9" viewBox="0 0 11 9"><rect x="0" y="0.5" width="11" height="8" fill="#fff"/><path d="M0.5 1l5 4 5-4" fill="none" stroke="#1bb3e8" stroke-width="1.2"/></svg>
          <span class="email">referrals@quillfordsurgeons.com.au</span>
        </div>
      </div>

      <div class="credentials">
        <span class="badge-shield"></span>
        <span class="credentials-text">Fellow of the Southern<br>College of Surgeons</span>
        <span class="badge-round"></span>
      </div>
    </section>
  </main>
</body>
</html>
```